Stationery Design Project for Marketing Consultancy

I have started a new consultancy business and require the following elements to be designed using existing logo:
• Business card
• Letterhead
• Envelope (DL, C4, C5)
• Microsoft word template for report writing
• A4 Presentation Folder
• Powerpoint template
COPY FOR FRONT AND BACK OF BUSINESS CARD
logo
'Measurable Marketing. Epic Results' slogan (but no need to use existing lockup with logo)
name, B Com. Mktg, Grad Cert Brand Mgmt, AMI (post nominal abbreviations in smaller font)
mobile: 04XX-XXX-XXX (I will give details to the winner to add)
website: www.tolvarin.com.au
email: info@tolvarin.com.au
COPY FOR LETTERHEAD
Logo
Company Name
Please, submit your designs that include business card, letterhead and envelope. Once selected the winner will be asked to complete the project by creating the rest of the artwork.
FINAL FILES
Print ready files to be supplied as well as Indesign files so that minor amends can be made if necessary in future.
• Layered vectors in EPS & PDF
• Screen quality JPEG & PNGs
ABOUT THE BUSINESS: TOLVARIN
I work with clients to understand their business challenges, developing and executing measurable marketing strategies tied to key business metrics. Services include:
Services include:
• Business planning and business development
• Marketing and brand strategy
• Insight-driven integrated campaigns
• Loyalty programs and retention marketing
• Marketing automation
• Direct marketing (traditional and digital)
• Content strategy and development
Hi everyone,
Target Market(s)
Corporate decision makers (heads of marketing, general managers etc) and small to medium sized business owners. Predominately male aged 35+
Industry/Entity Type
Marketing
Requirements
Must have
- BRAND PERSONALITY
The successful design will communicate brand personality. I am a professional, results-driven entrepreneur, but want to show off my creative flair.
MEMORABILITY
Looking for a unique and eye-catching design. Am considering special printing effects (die cuts, letterpress, interactive elements, embossing, foiling etc) or a striking minimalist approach.
Nice to have
- I have a mission that could be incorporated on reverse if room -
Turning insights into actions & passion into profit.
Should not have
- Use of pink or green.

```html
<!DOCTYPE html>
<html lang="en">
<head>
<meta charset="utf-8">
<title>Tolvarin Business Card</title>
<link rel="stylesheet" href="https://fonts.googleapis.com/css2?family=Open+Sans:wght@400;700&display=swap">
<style>
  :root {
    --backdrop: #e9e6e2;
    --card-top: #242424;
    --card-bottom: #141414;
    --ink-light: #f2f2f2;
    --ink-silver: #c9c9c9;
    --ink-muted: #d8d8d8;
  }
  * { margin: 0; padding: 0; box-sizing: border-box; }
  html, body {
    width: 1200px;
    height: 919px;
    overflow: hidden;
    background: var(--backdrop);
    font-family: "Open Sans", Arial, sans-serif;
  }
  .canvas {
    position: relative;
    width: 1200px;
    height: 919px;
    display: flex;
    align-items: center;
    justify-content: center;
    gap: 40px;
  }
  .card {
    position: relative;
    width: 520px;
    height: 297px;
    background: linear-gradient(160deg, var(--card-top), var(--card-bottom));
    border-radius: 2px;
    box-shadow: 0 6px 18px rgba(0, 0, 0, 0.18);
    overflow: hidden;
  }
  /* Back of card: contact details */
  .card-back .contact {
    position: absolute;
    left: 42px;
    top: 78px;
    color: var(--ink-muted);
    font-size: 14px;
    line-height: 1.4;
  }
  .contact .company-name {
    font-size: 19px;
    color: var(--ink-light);
    margin-bottom: 2px;
  }
  .contact .post-nominals {
    font-size: 13px;
  }
  .contact .website {
    font-weight: 700;
    color: var(--ink-light);
    font-size: 15px;
    margin-top: 2px;
  }
  .card-back .mini-name {
    position: absolute;
    right: 36px;
    top: 40px;
    font-size: 18px;
    font-weight: 700;
    color: var(--ink-silver);
    letter-spacing: 0.5px;
  }
  /* Front of card: name and slogan */
  .card-front .brand {
    position: absolute;
    left: 0;
    right: 0;
    top: 118px;
    text-align: center;
  }
  .brand .brand-name {
    font-size: 54px;
    font-weight: 700;
    color: var(--ink-silver);
    letter-spacing: 2px;
    line-height: 1;
  }
  .brand .slogan {
    margin-top: 10px;
    font-size: 13px;
    color: var(--ink-silver);
    letter-spacing: 1px;
    text-transform: uppercase;
  }
</style>
</head>
<body>
<main class="canvas">
  <section class="card card-back" aria-label="Business card, back">
    <div class="mini-name">TOLVARIN</div>
    <div class="contact">
      <p class="company-name">Company Name</p>
      <p class="role">Principal</p>
      <p class="post-nominals">B Com. Mktg, Grad Cert Brand Mgmt, AMI</p>
      <p class="mobile">mobile: 04XX-XXX-XXX</p>
      <p class="email">email: info@tolvarin.com.au</p>
      <p class="website">www.tolvarin.com.au</p>
    </div>
  </section>
  <section class="card card-front" aria-label="Business card, front">
    <div class="brand">
      <p class="brand-name">TOLVARIN</p>
      <p class="slogan">Sharper Strategy. Stronger Returns.</p>
    </div>
  </section>
</main>
</body>
</html>
```